One Pager Fact Sheet Design

I need a couple of headers and footer designed to use for information security fact sheets to give to customers. Similar to the one listed below.

```html
<!DOCTYPE html>
<html lang="en">
<head>
<meta charset="utf-8">
<title>Corvane Secure – Fact Sheet Letterhead</title>
<link rel="stylesheet" href="https://fonts.googleapis.com/css2?family=Hind:wght@400;500;700&display=swap">
<style>
  :root {
    --brand-red: #f0141c;
    --brand-red-deep: #c80d12;
    --brand-red-dark: #8e0a0d;
    --band-grey: #5b5b5b;
    --footer-grey: #cfcfcf;
    --ink: #1e1e1e;
    --paper: #ffffff;
    --watermark: #ececec;
    --icon-dark: #2b2b2b;
    --icon-orange: #f5a623;
    --icon-blue: #2a9fd8;
  }
  html, body {
    margin: 0;
    padding: 0;
    overflow: hidden;
    background: var(--paper);
  }
  .sheet {
    position: relative;
    width: 868px;
    height: 1200px;
    overflow: hidden;
    background: var(--paper);
    font-family: "Hind", sans-serif;
    color: var(--ink);
  }

  /* Header */
  .header {
    position: absolute;
    left: 0; top: 0;
    width: 868px;
    height: 233px;
    background:
      linear-gradient(135deg, transparent 48%, rgba(0,0,0,0.08) 50%, transparent 70%),
      linear-gradient(45deg, transparent 30%, rgba(0,0,0,0.06) 50%, transparent 52%),
      linear-gradient(90deg, var(--brand-red-deep) 0%, var(--brand-red) 35%, var(--brand-red) 60%, var(--brand-red-deep) 100%);
  }
  .header-visual {
    position: absolute;
    left: 545px; top: 0;
    width: 323px;
    height: 233px;
    background: linear-gradient(100deg, rgba(240,20,28,0) 0%, var(--brand-red-deep) 25%, var(--brand-red-dark) 70%, var(--brand-red-deep) 100%);
  }
  .brand {
    position: absolute;
    left: 36px; top: 96px;
    display: flex;
    align-items: center;
    gap: 14px;
  }
  .brand-dot {
    width: 66px; height: 66px;
    border-radius: 50%;
    border: 7px solid var(--paper);
    box-sizing: border-box;
  }
  .brand-name {
    font-weight: 700;
    font-size: 50px;
    line-height: 1;
    color: var(--paper);
    letter-spacing: -0.5px;
    padding-top: 8px;
  }
  .header-band {
    position: absolute;
    left: 0; top: 233px;
    width: 868px;
    height: 24px;
    background: var(--band-grey);
  }

  /* Body watermark */
  .watermark {
    position: absolute;
    left: 0; top: 560px;
    width: 868px;
    text-align: center;
    font-weight: 700;
    font-size: 96px;
    line-height: 1;
    color: var(--watermark);
  }

  /* Footer */
  .footer-rule {
    position: absolute;
    left: 0; top: 1129px;
    width: 868px; height: 5px;
    background: var(--brand-red);
  }
  .footer {
    position: absolute;
    left: 0; top: 1134px;
    width: 868px; height: 66px;
    background: var(--footer-grey);
    display: flex;
    align-items: center;
    padding: 0 16px;
    box-sizing: border-box;
    font-size: 12.6px;
    font-weight: 500;
    white-space: nowrap;
  }
  .contact {
    display: flex;
    align-items: center;
    gap: 5px;
    margin-right: 13px;
  }
  .contact:last-child { margin-right: 0; }
  .contact-icon { width: 17px; height: 17px; flex: none; }
  .social-dot {
    width: 16px; height: 16px;
    border-radius: 50%;
    background: var(--icon-blue);
  }
  .contact.social { margin-left: auto; }
</style>
</head>
<body>
<div class="sheet">
  <header class="header">
    <div class="header-visual" role="img" aria-label="Red-toned photo of hands typing on a laptop with a robotic hand and a security shield with keyhole"></div>
    <div class="brand">
      <div class="brand-dot"></div>
      <div class="brand-name">Corvane Secure</div>
    </div>
  </header>
  <div class="header-band"></div>

  <div class="watermark">Corvane</div>

  <div class="footer-rule"></div>
  <footer class="footer">
    <div class="contact">
      <svg class="contact-icon" viewBox="0 0 20 20" aria-hidden="true">
        <circle cx="10" cy="10" r="10" fill="var(--icon-dark)"/>
        <circle cx="10" cy="10" r="5.5" fill="none" stroke="#fff" stroke-width="1.4"/>
        <line x1="4.5" y1="10" x2="15.5" y2="10" stroke="#fff" stroke-width="1.2"/>
        <ellipse cx="10" cy="10" rx="2.4" ry="5.5" fill="none" stroke="#fff" stroke-width="1.2"/>
      </svg>
      <span>corvane.net&nbsp; corvanesecure.org</span>
    </div>
    <div class="contact">
      <svg class="contact-icon" viewBox="0 0 20 20" aria-hidden="true">
        <circle cx="10" cy="10" r="10" fill="var(--icon-dark)"/>
        <path d="M6 5.5 L14.5 9.5 L10.8 10.8 L9.5 14.5 Z" fill="#fff"/>
      </svg>
      <span>netlink.page/company/corvanesecure</span>
    </div>
    <div class="contact">
      <svg class="contact-icon" viewBox="0 0 20 20" aria-hidden="true">
        <circle cx="10" cy="10" r="10" fill="var(--icon-orange)"/>
        <path d="M5 8.5 Q10 4.5 15 8.5 L13.6 10 L11.8 9 L11.8 8 Q10 7.4 8.2 8 L8.2 9 L6.4 10 Z" fill="#fff"/>
        <rect x="7" y="10.5" width="6" height="4" rx="1" fill="#fff"/>
      </svg>
      <span>01632 960 418</span>
    </div>
    <div class="contact social">
      <span class="social-dot"></span>
      <span>@corvanesecure</span>
    </div>
  </footer>
</div>
</body>
</html>
```